New Business Card Design Project

Removed as project is complete.

Target Market(s)

Industry/Entity Type

Business

Requirements
Must have
• Removed as project is complete.
Nice to have
Should not have

```html
<!DOCTYPE html>
<html lang="en">
<head>
<meta charset="utf-8">
<title>Brightpath Compliance International – Business Card</title>
<link rel="stylesheet" href="https://fonts.googleapis.com/css2?family=Source+Sans+3:wght@400;600;700&display=swap">
<style>
  :root {
    --page-bg: #e9e7e4;
    --card-white: #ffffff;
    --card-black: #000000;
    --ink: #1a1a1a;
    --ink-soft: #333333;
    --brand-orange: #f08a1c;
    --brand-red: #e0262b;
    --brand-yellow: #ffc20e;
    --divider: #555555;
    --tagline: #ffffff;
  }
  * { box-sizing: border-box; margin: 0; padding: 0; }
  html, body {
    width: 1200px;
    height: 900px;
    overflow: hidden;
    background: var(--page-bg);
    font-family: "Source Sans 3", Arial, sans-serif;
  }
  .canvas { position: relative; width: 1200px; height: 900px; }

  .card {
    position: absolute;
    top: 274px;
    width: 538px;
    height: 326px;
    overflow: hidden;
    box-shadow: 0 2px 8px rgba(0,0,0,0.18);
  }
  .card--front { left: 54px; background: var(--card-white); }
  .card--back  { left: 618px; background: var(--card-black); }

  /* Front */
  .brand-mark {
    position: absolute;
    left: 108px;
    top: 66px;
    display: flex;
    align-items: center;
    gap: 10px;
  }
  .brand-mark__dot {
    width: 24px; height: 24px;
    border-radius: 50%;
    background: var(--brand-orange);
  }
  .brand-mark__name {
    font-size: 21px;
    font-weight: 400;
    color: var(--brand-orange);
    white-space: nowrap;
  }
  .person {
    position: absolute;
    left: 34px;
    top: 182px;
    font-size: 16px;
    line-height: 21px;
    color: var(--ink);
  }
  .person__name { font-weight: 700; }
  .divider {
    position: absolute;
    left: 180px;
    top: 180px;
    width: 1px;
    height: 72px;
    background: linear-gradient(to bottom, transparent, var(--divider) 20%, var(--divider) 80%, transparent);
  }
  .contact {
    position: absolute;
    left: 232px;
    top: 180px;
    list-style: none;
    font-size: 17px;
    line-height: 23.5px;
    color: var(--ink);
  }
  .contact li { display: flex; align-items: center; gap: 9px; }
  .contact svg { width: 15px; height: 15px; flex: none; }
  .address {
    position: absolute;
    left: 18px;
    top: 298px;
    font-size: 11px;
    color: var(--ink-soft);
  }
  .accent-band {
    position: absolute;
    left: 0; right: 0; bottom: 0;
    height: 11px;
    background: linear-gradient(to right, var(--brand-yellow), var(--brand-orange) 60%, var(--brand-red));
  }

  /* Back */
  .back-art {
    position: absolute;
    left: 0; top: 0;
    width: 150px;
    height: 326px;
  }
  .back-brand {
    position: absolute;
    left: 168px;
    top: 150px;
    display: flex;
    align-items: center;
    gap: 8px;
  }
  .back-brand__name {
    font-size: 20px;
    font-weight: 400;
    color: var(--brand-orange);
    white-space: nowrap;
  }
  .back-brand__dot {
    width: 14px; height: 14px;
    border-radius: 50%;
    background: var(--brand-orange);
  }
  .tagline {
    position: absolute;
    left: 168px;
    top: 221px;
    font-size: 19px;
    color: var(--tagline);
    white-space: nowrap;
  }
</style>
</head>
<body>
<main class="canvas">

  <section class="card card--front" aria-label="Business card front">
    <div class="brand-mark">
      <span class="brand-mark__dot"></span>
      <span class="brand-mark__name">Brightpath Compliance International</span>
    </div>

    <div class="person">
      <p class="person__name">Daniel Hartley</p>
      <p>Director</p>
      <p>BBus, CAMS</p>
    </div>

    <div class="divider"></div>

    <ul class="contact">
      <li>
        <svg viewBox="0 0 16 16" aria-hidden="true"><path d="M4 2h3l1 3-2 1a8 8 0 0 0 4 4l1-2 3 1v3a1 1 0 0 1-1 1A12 12 0 0 1 3 3a1 1 0 0 1 1-1z" fill="var(--brand-red)"/></svg>
        <span>+61 (0)200 555 014</span>
      </li>
      <li>
        <svg viewBox="0 0 16 16" aria-hidden="true"><rect x="1.5" y="3.5" width="13" height="9" fill="none" stroke="var(--brand-red)" stroke-width="1.6"/><path d="M1.5 3.5 8 9l6.5-5.5" fill="none" stroke="var(--brand-red)" stroke-width="1.6"/></svg>
        <span>name@brightpathcompliance.com</span>
      </li>
      <li>
        <svg viewBox="0 0 16 16" aria-hidden="true"><circle cx="8" cy="8" r="6.5" fill="none" stroke="var(--brand-red)" stroke-width="1.5"/><ellipse cx="8" cy="8" rx="2.8" ry="6.5" fill="none" stroke="var(--brand-red)" stroke-width="1.2"/><path d="M1.5 8h13" stroke="var(--brand-red)" stroke-width="1.2"/></svg>
        <span>www.brightpathcompliance.com</span>
      </li>
    </ul>

    <p class="address">Brightpath Compliance International Pty Ltd P.O. Box 2287, Bayside NSW 2150</p>
    <div class="accent-band"></div>
  </section>

  <section class="card card--back" aria-label="Business card back">
    <svg class="back-art" viewBox="0 0 150 326" role="img" aria-label="Large brand symbol decoration in red, orange and yellow">
      <defs>
        <linearGradient id="backArtTone" x1="0" y1="0" x2="1" y2="1">
          <stop offset="0" stop-color="#ffe08a"/>
          <stop offset="0.45" stop-color="#e0262b"/>
          <stop offset="1" stop-color="#ffc20e"/>
        </linearGradient>
      </defs>
      <rect width="150" height="326" fill="url(#backArtTone)"/>
    </svg>

    <div class="back-brand">
      <span class="back-brand__name">Brightpath Compliance International</span>
      <span class="back-brand__dot"></span>
    </div>
    <p class="tagline">Clear guidance for every compliance step...</p>
  </section>

</main>
</body>
</html>
```